Which Way Now? Listening for the Quiet Voice Within

I'm doing a series of ebooks that are 50 to 100 pages. The cover needs to be captivating because most of the traffic will be online. This book is about decision making and the steps that God offers to help us make good ones. If it works, perhaps we can silhouette or creatively show common questions: Is she the one? Is this job right for me? etc, or maybe just list some common areas: Entertainment, Music, Marriage, Sex, Modesty, etc. Just brainstorming.

```html
<!DOCTYPE html>
<html lang="en">
<head>
<meta charset="utf-8">
<title>Which Way Now? — Ebook Cover</title>
<link rel="stylesheet" href="https://fonts.googleapis.com/css2?family=Alfa+Slab+One&family=Archivo+Black&family=Work+Sans:wght@500&display=swap">
<style>
  :root {
    --page-bg: #ffffff;
    --cover-orange: #f0b467;
    --title-brown: #b35b0c;
    --text-white: #ffffff;
    --art-sky: #a3ecf6;
    --art-blue: #5f9fe8;
    --art-yellow: #f5d90e;
    --art-green: #5ee58b;
    --art-deep-green: #34a853;
    --art-pink: #f59be6;
    --art-coral: #f77b6c;
    --art-violet: #b48ae6;
    --art-amber: #f59413;
    --art-cream: #f6e68a;
    --art-rose: #d9507a;
  }
  * { margin: 0; padding: 0; box-sizing: border-box; }
  html, body {
    width: 1200px;
    height: 899px;
    overflow: hidden;
    background: var(--page-bg);
  }
  .cover {
    position: absolute;
    left: 311px;
    top: 43px;
    width: 574px;
    height: 811px;
    background: var(--cover-orange);
  }
  .cover-title {
    position: absolute;
    top: 20px;
    left: 0;
    width: 100%;
    text-align: center;
    font-family: "Alfa Slab One", "Ultra", serif;
    font-weight: 400;
    font-size: 34px;
    line-height: 42px;
    letter-spacing: 0.5px;
    color: var(--title-brown);
    text-transform: uppercase;
  }
  .cover-art {
    position: absolute;
    left: 53px;
    top: 70px;
    width: 468px;
    height: 662px;
    border: 1.5px solid var(--text-white);
    background-color: var(--cover-orange);
    background-image:
      radial-gradient(ellipse 22% 16% at 8% 5%, var(--art-coral) 0%, transparent 100%),
      radial-gradient(ellipse 30% 22% at 20% 25%, var(--art-sky) 30%, transparent 100%),
      radial-gradient(ellipse 16% 22% at 45% 18%, var(--art-yellow) 35%, transparent 100%),
      radial-gradient(ellipse 14% 20% at 63% 22%, var(--art-pink) 30%, transparent 100%),
      radial-gradient(ellipse 18% 12% at 86% 22%, var(--art-violet) 10%, transparent 100%),
      radial-gradient(ellipse 24% 34% at 88% 40%, var(--art-green) 40%, transparent 100%),
      radial-gradient(ellipse 10% 10% at 94% 62%, var(--art-blue) 20%, transparent 100%),
      radial-gradient(ellipse 20% 18% at 36% 48%, var(--art-amber) 20%, transparent 100%),
      radial-gradient(ellipse 20% 14% at 22% 66%, var(--art-rose) 20%, transparent 100%),
      radial-gradient(ellipse 22% 18% at 30% 82%, var(--art-pink) 10%, transparent 100%),
      radial-gradient(ellipse 22% 16% at 18% 95%, var(--art-cream) 20%, transparent 100%),
      radial-gradient(ellipse 18% 24% at 80% 92%, var(--art-blue) 25%, transparent 100%),
      radial-gradient(ellipse 30% 30% at 72% 84%, var(--art-pink) 40%, transparent 100%),
      radial-gradient(ellipse 14% 10% at 86% 72%, var(--art-deep-green) 10%, transparent 100%);
  }
  .cover-subtitle {
    position: absolute;
    top: 746px;
    left: 0;
    width: 100%;
    text-align: center;
    font-family: "Archivo Black", sans-serif;
    font-size: 18.5px;
    line-height: 22px;
    letter-spacing: 0.6px;
    color: var(--text-white);
    text-transform: uppercase;
  }
  .cover-author {
    position: absolute;
    top: 770px;
    left: 0;
    width: 100%;
    text-align: center;
    font-family: "Work Sans", sans-serif;
    font-weight: 500;
    font-size: 12px;
    line-height: 14px;
    color: var(--text-white);
  }
</style>
</head>
<body>
  <main class="cover">
    <h1 class="cover-title">Which Way Now?</h1>
    <div class="cover-art" role="img" aria-label="Colourful illustration of a maze of impossible staircases, arches and platforms in bright pastel colours with halftone shading"></div>
    <p class="cover-subtitle">Listening for the Quiet Voice Within</p>
    <p class="cover-author">Dr Miles Harper</p>
  </main>
</body>
</html>
```